Home Page Design (+50 More Pages To Winning Designer!)

We have a 50+ page website, but we're starting with the home page. The winning designer will get all 50+ pages to design as a 2nd project, so make sure you do your best!

Velorane is in the private jet industry and needs a re-designed website.

We have created the structure for the website and content inside of Frandle.io (THESE ARE ONLY ROUGH A.I. GENERATED WIREFRAMES AND DO NOT NEED TO BE FOLLOWED EXACTLY) - https://www.frandle.io/app/project/K482915_qWmRtZaLs-KDnHoUvvy82QJ5cfhaR61trkwqlDV3Hm

Take the content from the 'Home Page' under the 'Wireframe' tab on the Frandle.io link above, but feel free to re-design the page in a better way as these are only A.I. generated wireframes.

We want a DARK theme.... High quality, luxurious feel, greyscale colors. Attached is a brand guideline (BUT THIS IS NOT A 100% BRAND GUIDELINE, YOU CAN CHANGE COLORS AND FONTS AND MAKE CHANGES IF YOU HAVE BETTER IDEAS) and attached is our logo. We are also attaching some examples of other apps and websites to give you a guideline of what we're looking for for this design project.

The final design MUST communicate luxury using high-quality imagery of large cabin luxurious private jets.
Updates

ENTRIES THAT DO NOT FOLLOW THE PROJECT BRIEF WILL BE AUTOMATICALLY DISCARDED. FOLLOW THE INSTRUCTIONS!

Industry/Entity Type

Travel

Number of Pages Required

1 page

Font styles to use
Sans Serif

Colors

Designer to choose colors to be used in the design.

Requirements
Must have
• Follow wireframe and use content in wireframe (see Frandle.io link)

```html
<!DOCTYPE html>
<html lang="en">
<head>
<meta charset="utf-8">
<title>Velorane — Luxury Private Jet Travel</title>
<link rel="stylesheet" href="https://fonts.googleapis.com/css2?family=Roboto:wght@300;400;500;700&display=swap">
<style>
:root{
  --bg:#262626;
  --bg-alt:#2f2f2f;
  --bg-deep:#1c1c1c;
  --card:#1e1e1e;
  --white:#ffffff;
  --text:#e9e9e9;
  --muted:#8d8d8d;
  --line:#4a4a4a;
  --star:#e4b934;
}
*{box-sizing:border-box;margin:0;padding:0}
html,body{width:1200px;height:4898px;overflow:hidden}
body{background:var(--bg);color:var(--text);font-family:"Roboto",sans-serif;position:relative}
.abs{position:absolute}
.section{position:absolute;left:0;width:1200px;overflow:hidden}
h1,h2,h3{font-weight:400;color:var(--white)}
.muted{color:var(--muted)}
.btn{display:inline-flex;align-items:center;justify-content:center;height:26px;padding:0 16px;font-size:10px;border-radius:2px;font-family:"Roboto",sans-serif;white-space:nowrap}
.btn-solid{background:var(--white);color:#111;border:1px solid var(--white)}
.btn-ghost{background:transparent;color:var(--white);border:1px solid #9a9a9a}
.btn-row{display:flex;gap:10px}
.icon-disc{width:38px;height:38px;border-radius:50%;background:var(--white);display:flex;align-items:center;justify-content:center}

/* image frames: clean rounded mask, large radius on the outer side */
.photo{position:absolute;overflow:hidden}
.frame-right{border-radius:10px 140px 140px 10px}
.frame-left{border-radius:140px 10px 10px 140px}

/* nav */
.nav{position:absolute;top:0;left:0;width:1200px;height:66px;z-index:5}
.brand{position:absolute;left:153px;top:20px;font-size:22px;font-weight:300;color:var(--white);display:flex;align-items:center;gap:6px}
.brand-mark{width:12px;height:12px;background:var(--white)}
.nav-links{position:absolute;right:155px;top:20px;display:flex;align-items:center;gap:20px;font-size:10px;color:var(--white)}
.nav-links .btn{height:22px;padding:0 14px;font-size:9px}

/* hero */
.hero{top:0;height:625px;background:linear-gradient(#1d1d1d,#242424)}
.hero-media{position:absolute;left:0;top:235px;width:1200px;height:385px;background:linear-gradient(180deg,#262626 0%,#4a4a4e 30%,#3a3436 60%,#5a4547 85%,#2b2526 100%);border-radius:0 0 50% 50%/0 0 70px 70px}
.hero-title{position:absolute;top:118px;width:100%;text-align:center;font-size:21px}
.hero-text{position:absolute;top:153px;left:340px;width:520px;text-align:center;font-size:10px;line-height:15px}
.hero .btn-row{position:absolute;top:205px;left:0;width:100%;justify-content:center}

/* split sections */
.split-title{font-size:22px;line-height:28px;color:var(--white)}
.split-text{font-size:10px;line-height:14px;margin-top:16px}
.feature-row{display:flex;gap:30px;margin-top:20px}
.feature{width:92px;font-size:9px;line-height:12px;color:var(--white)}
.feature .icon-disc{margin-bottom:8px}

.ownership{top:625px;height:440px;background:var(--bg)}
.ownership .copy{position:absolute;left:255px;top:78px;width:330px}
.ownership .btn-row{margin-top:28px}

.programs{top:1065px;height:471px;background:var(--bg-alt)}
.program-list{position:absolute;left:640px;top:128px;border-left:1px solid var(--line);padding-left:12px;width:300px}
.program{margin-bottom:30px}
.program h3{font-size:13px}
.program p{font-size:10px;line-height:13px;margin-top:6px}

.luxury{top:1536px;height:478px;background:var(--bg)}
.luxury .copy{position:absolute;left:255px;top:100px;width:390px}
.eyebrow{font-size:9px;font-weight:500;color:var(--white)}
.perk-row{display:flex;gap:30px;margin-top:20px}
.perk{display:flex;gap:10px;width:150px}
.perk .icon-disc{flex:0 0 38px}
.perk h4{font-size:10px;font-weight:500;color:var(--white)}
.perk p{font-size:9px;line-height:12px;margin-top:4px}
.luxury .btn-row{margin-top:28px}

.services{top:2014px;height:584px;background:var(--bg-deep)}
.services .head{position:absolute;top:86px;width:100%;text-align:center}
.services h2{font-size:22px;margin-top:6px}
.services .lead{font-size:10px;line-height:14px;width:520px;margin:10px auto 0}
.service{position:absolute;top:222px;width:200px;text-align:center}
.service .icon-disc{width:48px;height:48px;margin:0 auto}
.service h3{font-size:11px;font-weight:500;margin-top:12px;line-height:14px}
.service p{font-size:9px;line-height:12px;margin-top:6px}
.services .btn-row{position:absolute;top:380px;width:100%;justify-content:center}

.cta-card{position:absolute;background:var(--card);border-radius:12px;text-align:center}
.cta-card h2{font-size:22px;color:var(--white)}
.cta-card p{font-size:10px;line-height:14px}
.cta-card .btn-row{justify-content:center}
.cta-top{left:328px;top:2498px;width:544px;height:184px;z-index:3;border:1px solid #262626}

.testimonial{top:2598px;height:480px;background:var(--bg)}
.quote-disc{position:absolute;left:575px;top:180px;width:48px;height:48px;border-radius:50%;border:2px solid var(--white);display:flex;align-items:center;justify-content:center;font-size:24px;font-weight:700;color:var(--white)}
.stars{position:absolute;top:245px;width:100%;text-align:center;color:var(--star);font-size:14px;letter-spacing:3px}
.testimonial blockquote{position:absolute;top:275px;left:300px;width:600px;text-align:center;font-size:9.5px;line-height:17px;color:var(--text)}
.author{position:absolute;top:365px;left:0;width:100%;display:flex;justify-content:center;align-items:center;gap:10px;font-size:9px}
.avatar{width:30px;height:30px;border-radius:50%;background:linear-gradient(135deg,#8a7a70,#3c3633)}
.client-badge{width:90px;height:30px;background:var(--white);border-radius:3px;margin-left:12px}
.next{position:absolute;right:170px;width:14px;height:14px}

.trusted{top:3078px;height:340px;background:linear-gradient(180deg,#1c1c1c,#222 60%,#262626)}
.trusted h3{position:absolute;top:88px;width:100%;text-align:center;font-size:11px}
.logo-row{position:absolute;top:132px;left:266px;display:flex;gap:16px}
.logo-tile{width:122px;height:66px;background:var(--white);border-radius:6px;display:flex;align-items:center;justify-content:center}
.logo-tile span{width:60px;height:14px;background:#d6d6d6;border-radius:2px}
.trusted .view-all{position:absolute;top:244px;left:567px;height:22px;font-size:9px;padding:0 16px}

.newsletter{left:300px;top:3432px;width:598px;height:216px;background:#161616;border-radius:8px;overflow:hidden}
.newsletter h2{position:absolute;left:42px;top:44px;font-size:22px;line-height:28px;color:var(--white)}
.newsletter .sub{position:absolute;left:42px;top:104px;font-size:9px}
.field{position:absolute;left:42px;top:122px;width:314px;height:30px;background:var(--white);border-radius:2px;font-size:9px;color:#999;padding:0 10px;display:flex;align-items:center;justify-content:space-between}
.newsletter .legal{position:absolute;left:42px;top:162px;font-size:8px}
.newsletter .art{position:absolute;left:380px;top:30px;width:170px;height:130px;border-radius:65px;background:radial-gradient(ellipse at center,#5e5e5e,#262626 70%)}

.faq{position:absolute;left:604px;top:3768px;width:360px}
.faq h2{font-size:22px}
.faq .intro{font-size:10px;margin-top:8px}
.faq-item{border-bottom:1px solid #3c3c3c;padding:14px 12px 12px;font-size:9.5px;color:var(--white);display:flex;justify-content:space-between}
.faq-item.open{flex-wrap:wrap}
.faq-item.open p{flex-basis:100%;color:var(--muted);font-size:8.5px;line-height:12px;margin-top:12px}
.faq-list{margin-top:24px}
.still{position:absolute;left:604px;top:4176px;width:300px}
.still h3{font-size:13px}
.still p{font-size:9px;margin-top:4px}
.still .btn{position:absolute;left:212px;top:2px;height:24px;font-size:9px}
.cta-bottom{left:302px;top:4307px;width:598px;height:215px}

.footer{top:4578px;height:320px;background:linear-gradient(180deg,#262626,#151515 40%,#121212)}
.footer .brand{top:106px}
.foot-col{position:absolute;top:100px;font-size:8.5px;line-height:16px;color:var(--muted)}
.foot-col h4{font-size:10px;font-weight:500;color:var(--white);margin-bottom:6px}
.foot-field{width:238px;height:26px;background:var(--white);border-radius:2px;font-size:8px;color:#999;display:flex;align-items:center;justify-content:space-between;padding:0 8px;margin-top:8px}
.foot-bottom{position:absolute;top:288px;left:153px;width:890px;display:flex;justify-content:space-between;font-size:8px;color:var(--muted)}
.foot-bottom .legal-links{display:flex;gap:14px}
.social{display:flex;gap:8px}
.social span{width:7px;height:7px;border-radius:50%;background:var(--white)}
</style>
</head>
<body>

<header class="nav">
  <div class="brand">Velorane <span class="brand-mark"></span></div>
  <nav class="nav-links">
    <span>Aircraft</span><span>Programs</span><span>Why Velorane</span><span>Lifestyle &#8964;</span>
    <span class="btn btn-ghost">Inquiry</span><span class="btn btn-solid">Sign Up</span>
  </nav>
</header>

<section class="section hero">
  <div class="hero-media" role="img" aria-label="Private jet flying above a dark mountain range at dusk"></div>
  <h1 class="hero-title">Experience the Ultimate in Luxury Jet Travel</h1>
  <p class="hero-text muted">Velorane offers fractional jet ownership, jet card programs, private jet lease programs, all access programs, helicopter access programs, and by the seat charter flights. Discover the perfect flight program for your needs.</p>
  <div class="btn-row"><span class="btn btn-solid">Explore</span><span class="btn btn-ghost">Learn More</span></div>
</section>

<section class="section ownership">
  <div class="copy">
    <h2 class="split-title">Experience the Luxury of<br>Fractional Jet Ownership</h2>
    <p class="split-text muted">With Velorane's fractional jet ownership program, you can enjoy the benefits of private jet travel without the hassle and expense of owning a whole aircraft. Our program offers flexibility, convenience, and access to a fleet of luxurious jets, allowing you to travel in style and comfort.</p>
    <div class="feature-row">
      <div class="feature"><div class="icon-disc"><svg width="18" height="18" viewBox="0 0 24 24"><path d="M2 14l20-6-4 8-6-2-3 5-1-6z" fill="#222"/></svg></div>Flexible Ownership Options</div>
      <div class="feature"><div class="icon-disc"><svg width="18" height="18" viewBox="0 0 24 24"><rect x="4" y="6" width="16" height="14" rx="2" fill="#222"/><rect x="7" y="3" width="2" height="5" fill="#222"/><rect x="15" y="3" width="2" height="5" fill="#222"/></svg></div>Convenient Booking Process</div>
      <div class="feature"><div class="icon-disc"><svg width="18" height="18" viewBox="0 0 24 24"><path d="M12 2l2 8 8 3-8 1-2 8-2-8-8-1 8-3z" fill="#222"/></svg></div>Luxurious Fleet of Jets</div>
    </div>
    <div class="btn-row"><span class="btn btn-solid">Learn More</span><span class="btn btn-ghost">Sign Up</span></div>
  </div>
  <div class="photo frame-right" role="img" aria-label="Portrait of a businessman in a grey suit" style="left:782px;top:86px;width:340px;height:335px;background:linear-gradient(135deg,#5a4a40,#2c2624 60%,#6e635c)"></div>
</section>

<section class="section programs">
  <div class="photo frame-right" role="img" aria-label="Businessman in a leather armchair floating above a city among jets" style="left:255px;top:84px;width:290px;height:331px;background:linear-gradient(160deg,#b8966e,#6e6052 50%,#3a3634)"></div>
  <div class="program-list">
    <div class="program"><h3>Flexible Ownership Options Available</h3><p class="muted">Choose from a variety of ownership programs and enjoy the freedom to fly on your own terms.</p></div>
    <div class="program"><h3>Convenient Jet Card Programs</h3><p class="muted">Access a fleet of private jets with our exclusive jet card programs, offering flexibility and convenience.</p></div>
    <div class="program"><h3>Flexible Lease Programs</h3><p class="muted">Experience the luxury of private jet travel without the commitment with our flexible lease programs.</p></div>
  </div>
</section>

<section class="section luxury">
  <div class="copy">
    <div class="eyebrow">Experience</div>
    <h2 class="split-title" style="margin-top:6px">Unparalleled Luxury and<br>Convenience for Private Aviation</h2>
    <p class="split-text muted" style="width:340px">Discover the ultimate in luxury and convenience with Velorane. Our exclusive private aviation solutions provide you with unparalleled access to the world of private jets, ensuring a seamless and extraordinary travel experience.</p>
    <div class="perk-row">
      <div class="perk"><div class="icon-disc"><svg width="18" height="18" viewBox="0 0 24 24"><path d="M4 11h4v9H4zM10 20V10l4-7 2 2-1 5h5l-2 10z" fill="#222"/></svg></div><div><h4>Convenience</h4><p class="muted">Enjoy hassle-free travel with our flexible scheduling and personalized services.</p></div></div>
      <div class="perk"><div class="icon-disc"><svg width="18" height="18" viewBox="0 0 24 24"><path d="M6 3h12l4 6-10 12L2 9z" fill="#222"/></svg></div><div><h4>Luxury</h4><p class="muted">Indulge in the lavish amenities and exquisite interiors of our private jets.</p></div></div>
    </div>
    <div class="btn-row"><span class="btn btn-solid">Learn More</span><span class="btn btn-ghost">Sign Up</span></div>
  </div>
  <div class="photo frame-right" role="img" aria-label="Smiling pilot wearing a headset in the cockpit" style="left:782px;top:87px;width:340px;height:333px;background:linear-gradient(135deg,#2a2a2a,#5e5048 50%,#3a3430)"></div>
</section>

<section class="section services">
  <div class="head">
    <div class="eyebrow">Luxury</div>
    <h2>Experience the Ultimate in Private Jet Travel</h2>
    <p class="lead muted">Velorane offers a wide range of exclusive services to meet your private jet travel needs. From fractional jet ownership to on-demand charter flights, we provide the highest level of luxury and convenience.</p>
  </div>
  <div class="service" style="left:300px"><div class="icon-disc"><svg width="22" height="22" viewBox="0 0 24 24"><path d="M2 14l20-6-4 8-6-2-3 5-1-6z" fill="#222"/></svg></div><h3>On-Demand Charter</h3><p class="muted">Fly anywhere, anytime with our on-demand charter service.</p></div>
  <div class="service" style="left:500px"><div class="icon-disc"><svg width="22" height="22" viewBox="0 0 24 24"><circle cx="12" cy="12" r="9" fill="none" stroke="#222" stroke-width="2"/><path d="M3 12h18M12 3v18" stroke="#222" stroke-width="2"/></svg></div><h3>Global Medical Response &amp;<br>Recovery</h3><p class="muted">We provide specialized medical transportation services worldwide.</p></div>
  <div class="service" style="left:700px"><div class="icon-disc"><svg width="22" height="22" viewBox="0 0 24 24"><path d="M11 2h2v8l8 4v2l-8-2v5l3 2v1l-4-1-4 1v-1l3-2v-5l-8 2v-2l8-4z" fill="#222"/></svg></div><h3>Fractional Jet Ownership</h3><p class="muted">Enjoy the benefits of owning a private jet without the hassles.</p></div>
  <div class="btn-row"><span class="btn btn-solid">Learn More</span><span class="btn btn-ghost">Sign Up</span></div>
</section>

<section class="section testimonial">
  <div class="quote-disc">&#8220;</div>
  <div class="stars">&#9733;&#9733;&#9733;&#9733;&#9733;</div>
  <blockquote>Lorem Ipsum Is Simply Dummy Text Of The Printing And Typesetting Industry. Lorem Ipsum Has Been The Industry's Standard Dummy Text Ever Since The 1500s, When An Unknown Printer Took A Galley Of Type And Scrambled It To Make A Type Specimen Book. It Has Survived Not Only Five Centuries, But Also The Leap Into Electronic Typesetting, Remaining Essentially Unchanged.</blockquote>
  <svg class="next" style="top:322px" viewBox="0 0 14 14"><path d="M5 2l5 5-5 5" fill="none" stroke="#fff" stroke-width="1.4"/></svg>
  <div class="author"><div class="avatar" role="img" aria-label="Client portrait"></div><div><div style="color:#fff;font-weight:500">Elias Marrow</div><div class="muted">CEO, Norvale Group</div></div><div class="client-badge"></div></div>
</section>

<div class="cta-card cta-top">
  <h2 style="margin-top:44px">Experience luxury travel like never before</h2>
  <p class="muted" style="margin-top:8px">Contact us today to book your exclusive jet experience</p>
  <div class="btn-row" style="margin-top:20px"><span class="btn btn-solid">Learn More</span><span class="btn btn-ghost">Sign Up</span></div>
</div>

<section class="section trusted" role="img" aria-label="Faint private jet in a dark sky behind partner logos">
  <h3>Trusted By Top-Tier Companies Around The Globe</h3>
  <div class="logo-row">
    <div class="logo-tile"><span></span></div><div class="logo-tile"><span></span></div><div class="logo-tile"><span></span></div><div class="logo-tile"><span></span></div><div class="logo-tile"><span></span></div>
  </div>
  <svg class="next" style="top:158px" viewBox="0 0 14 14"><path d="M5 2l5 5-5 5" fill="none" stroke="#fff" stroke-width="1.4"/></svg>
  <span class="btn btn-ghost view-all">View All</span>
</section>

<div class="abs newsletter">
  <h2>Subscribe to our<br>Newsletter</h2>
  <p class="sub muted">Stay updated with exclusive offers and industry news</p>
  <div class="field">Your email address<svg width="12" height="12" viewBox="0 0 24 24"><path d="M2 12l20-9-7 19-3-8z" fill="#111"/></svg></div>
  <p class="legal muted">By joining, you agree to our Terms and Conditions</p>
  <div class="art" role="img" aria-label="Folded paper plane illustration"></div>
</div>

<div class="photo frame-left" role="img" aria-label="Traveller at a jet window with a large question mark" style="left:232px;top:3766px;width:320px;height:389px;background:linear-gradient(135deg,#3a3a3a,#6e6a64 45%,#2a2a2a)"></div>

<div class="faq">
  <h2>Frequently</h2>
  <p class="intro muted">Find answers to common questions about Velorane's services and programs.</p>
  <div class="faq-list">
    <div class="faq-item"><span>What is Velorane?</span><span>+</span></div>
    <div class="faq-item open"><span>How it works?</span><span>&#8211;</span><p>Velorane is a company that offers fractional jet ownership, jet card programs, private jet lease programs, all access programs, helicopter access programs, and by the seat charter flights. We provide flexible and convenient options for individuals and businesses to access private aviation services.</p></div>
    <div class="faq-item"><span>Why choose Velorane?</span><span>+</span></div>
    <div class="faq-item"><span>How to book?</span><span>+</span></div>
    <div class="faq-item"><span>What are the benefits?</span><span>+</span></div>
  </div>
</div>
<div class="still">
  <h3>Still have questions?</h3>
  <p class="muted">Contact us for more information</p>
  <span class="btn btn-ghost">Contact</span>
</div>

<div class="cta-card cta-bottom" style="background:#1c1c1c">
  <h2 style="margin-top:44px">Experience luxury travel like never before</h2>
  <p class="muted" style="margin:14px auto 0;width:500px">Discover the ultimate in private jet travel with Velorane. Whether you're looking for fractional jet ownership, jet card programs, private jet lease programs, all access programs, helicopter access programs, or by the seat charter flights, we have the perfect solution for your travel needs.</p>
  <div class="btn-row" style="margin-top:16px"><span class="btn btn-solid">Book</span><span class="btn btn-ghost">Contact</span></div>
</div>

<footer class="section footer" role="img" aria-label="Dark silhouette of a private jet on the tarmac">
  <div class="brand">Velorane <span class="brand-mark"></span></div>
  <div class="foot-col" style="left:380px"><h4>About Us</h4>Charter<br>Fleet<br>Destinations<br>Pricing<br>Contact</div>
  <div class="foot-col" style="left:507px"><h4>Services</h4>Private Jets<br>Helicopters<br>Jet Cards<br>Membership<br>FAQ</div>
  <div class="foot-col" style="left:649px"><h4>Terms</h4>Privacy<br>Careers<br>Press<br>Blog<br>Support</div>
  <div class="foot-col" style="left:759px"><h4>Subscribe to our Newsletter</h4>Join our mailing list for the latest updates.
    <div class="foot-field">Enter email address<svg width="12" height="12" viewBox="0 0 24 24"><path d="M2 12l20-9-7 19-3-8z" fill="#111"/></svg></div>
    <div style="font-size:7.5px;line-height:10px;margin-top:6px">By subscribing, you agree to our Privacy Policy and<br>consent to receive updates.</div>
  </div>
  <div class="foot-bottom">
    <div class="legal-links"><span>&copy; 2024 Velorane. All rights reserved.</span><span>Privacy Policy</span><span>Terms of Service</span><span>Cookie Settings</span></div>
    <div class="social"><span></span><span></span><span></span><span></span><span></span></div>
  </div>
</footer>

</body>
</html>
```